Satchel & Sundial needs new business card design

I need a new business card design. I'm looking for out-of-the-box design which represents the freedom of being a location independent entrepreneur.
I offer coaching, retreats and trips.
I would like to see designs with and without the photo.
Colors I use are black (#000000), green (#25A796) and brown (#D7C38C)
Website satchelandsundial.example

Target Market(s)

location independent entrepreneurs, digital nomads, people looking to swap the 9 to 5 for a lifestyle business

Industry/Entity Type

Business

Contact Information for Business Card

Dorota Falkner
Your Lifestyle Business Coach, Retreat & Trip Leader
http://satchelandsundial.example
hello@satchelandsundial.example
Live a life you don't need a holiday from

Font styles to use
Serif
Sans Serif

Requirements
Must have
• One side should contain only the logo. I would also consider having the "Live a life you don't need a holiday from" on that side too (depending on how it looks)
• Please show both sides on the designs.

```html
<!DOCTYPE html>
<html lang="en">
<head>
<meta charset="utf-8">
<title>Satchel &amp; Sundial — Business Card</title>
<link rel="stylesheet" href="https://fonts.googleapis.com/css2?family=Amatic+SC:wght@700&family=Caveat:wght@500&display=swap">
<style>
  :root {
    --ink: #000000;
    --green: #25A796;
    --gold: #D7C38C;
    --gold-light: #d9c486;
    --gold-dark: #c6ae6c;
    --backdrop: #e6e6e6;
    --photo-leaf: #7f9468;
    --photo-shade: #4f5f45;
    --photo-light: #c9d1bd;
  }
  * { box-sizing: border-box; margin: 0; padding: 0; }
  html, body { width: 1200px; height: 576px; overflow: hidden; }
  body { background: var(--backdrop); position: relative; }

  .card {
    position: absolute;
    top: 138px;
    width: 486px;
    height: 294px;
    border-radius: 8px;
    overflow: hidden;
    background: linear-gradient(180deg, var(--gold-light), var(--gold-dark));
    color: var(--ink);
  }
  .card--front { left: 82px; }
  .card--back { left: 602px; width: 482px; }

  .wordmark {
    font-family: "Amatic SC", sans-serif;
    font-weight: 700;
    color: var(--ink);
    letter-spacing: 1px;
    line-height: 1;
    white-space: nowrap;
  }
  .card--front .wordmark {
    position: absolute;
    left: 0; right: 0;
    top: 98px;
    text-align: center;
    font-size: 50px;
  }

  .portrait {
    position: absolute;
    left: 0; top: 0;
    width: 216px;
    height: 100%;
    background:
      radial-gradient(ellipse at 45% 55%, var(--photo-light) 0 22%, transparent 45%),
      linear-gradient(160deg, var(--photo-leaf), var(--photo-shade));
    -webkit-mask-image: linear-gradient(90deg, #000 82%, transparent 100%);
            mask-image: linear-gradient(90deg, #000 82%, transparent 100%);
  }

  .details {
    position: absolute;
    right: 38px;
    top: 0;
    width: 260px;
    height: 100%;
    text-align: right;
  }
  .details > * {
    position: absolute;
    right: 0;
    line-height: 1;
    white-space: nowrap;
  }
  .details .wordmark { top: 36px; font-size: 29px; }
  .person-name {
    top: 118px;
    font-family: "Amatic SC", sans-serif;
    font-weight: 700;
    font-size: 24px;
    letter-spacing: 1px;
  }
  .person-role, .contact-line {
    font-family: "Caveat", cursive;
    font-weight: 500;
  }
  .person-role { top: 147px; font-size: 11px; }
  .contact-line { font-size: 12.5px; }
  .contact-line--email { top: 175px; }
  .contact-line--web { top: 197px; }
  .motto {
    top: 241px;
    font-family: "Amatic SC", sans-serif;
    font-weight: 700;
    font-size: 16px;
    letter-spacing: 0.5px;
  }
</style>
</head>
<body>
  <section class="card card--front" aria-label="Card front">
    <div class="wordmark">Satchel &amp; Sundial</div>
  </section>

  <section class="card card--back" aria-label="Card back">
    <div class="portrait" role="img" aria-label="Portrait photo of the coach outdoors under trees, holding a small chalkboard sign"></div>
    <div class="details">
      <div class="wordmark">Satchel &amp; Sundial</div>
      <div class="person-name">Dorota Falkner</div>
      <div class="person-role">Your Lifestyle Business Coach, Retreat and Trip Leader</div>
      <div class="contact-line contact-line--email">hello@satchelandsundial.example</div>
      <div class="contact-line contact-line--web">www.satchelandsundial.example</div>
      <div class="motto">Live a life you don't need a holiday from</div>
    </div>
  </section>
</body>
</html>
```